Naturopath Practitioner Card Design

I am a naturopath needing a design for a business card mainly to show that I am a naturopath and have some contact details to give to prospective clients. I am open minded about the design and what is on the second side of the card whether it just be some artwork or space for details, appointment times etc. Naturopathy is the practice of natural medicine that uses a holistic approach and incorporates herbal and nutritional medicine.

Industry/Entity Type

Business

Contact Information for Business Card

Tom Rudd NaturopathBHSc (Naturopathy) Member WHPG 0487 925 316 tom.rudd@mailexample.com www.tomruddnaturopathy.example.au

Requirements
Nice to have
• Would prefer some kind of original pattern/art work/logo rather than an image, not fussed if its very simple/basic
• I am open to any colour but think I would prefer a more earthy sandy clay etc type style than the greens that are commonly associated with naturopathy.
Should not have
• Don't really want to have generic stock images on it

```html
<!DOCTYPE html>
<html lang="en">
<head>
<meta charset="utf-8">
<title>Tom Rudd Naturopath – Business Card</title>
<link href="https://fonts.googleapis.com/css2?family=Open+Sans:wght@400;600;700&display=swap" rel="stylesheet">
<style>
  :root {
    --page-bg: #e9ebe6;
    --card-white: #ffffff;
    --leaf-green: #2fa52a;
    --leaf-deep: #3f8f1f;
    --wash-light: #f2fbe6;
    --wash-mid: #d6efb0;
    --ink: #1c1c1c;
    --box-line: #6b6b6b;
  }
  * { box-sizing: border-box; margin: 0; padding: 0; }
  html, body {
    width: 1200px; height: 844px; overflow: hidden;
    background: var(--page-bg);
    font-family: "Open Sans", Arial, sans-serif;
  }
  .sheet {
    position: relative; width: 1200px; height: 844px;
    display: flex; align-items: center; justify-content: center; gap: 50px;
  }
  .card {
    position: relative; width: 525px; height: 300px; overflow: hidden;
    box-shadow: 0 6px 18px rgba(0,0,0,.18);
  }

  /* Front */
  .card-front {
    background: linear-gradient(115deg, var(--wash-mid) 0%, #e4f5c8 35%, var(--wash-light) 65%, #fafff4 100%);
  }
  .front-artwork {
    position: absolute; inset: 0;
    background:
      radial-gradient(ellipse 70px 110px at 150px 200px, rgba(120,190,40,.7), rgba(120,190,40,0) 100%),
      radial-gradient(ellipse 120px 45px at 250px 170px, rgba(150,205,60,.6), rgba(150,205,60,0) 100%),
      radial-gradient(ellipse 50px 110px at 10px 110px, rgba(90,170,30,.75), rgba(90,170,30,0) 100%),
      radial-gradient(ellipse 200px 160px at 150px 280px, rgba(190,230,120,.55), rgba(190,230,120,0) 100%);
  }
  .front-details {
    position: absolute; right: 30px; top: 60px; text-align: right; color: var(--ink);
  }
  .holder-name { font-size: 20px; font-weight: 600; color: var(--leaf-green); line-height: 1.2; }
  .holder-role { font-size: 13px; margin-top: 2px; }
  .holder-credentials { font-size: 13px; margin-top: 14px; }
  .contact-list { list-style: none; margin-top: 28px; font-size: 14px; }
  .contact-list li { display: flex; justify-content: flex-end; align-items: center; gap: 6px; margin-bottom: 12px; }
  .contact-icon { width: 12px; height: 12px; flex: none; }

  /* Back */
  .card-back { background: var(--card-white); }
  .foliage {
    position: absolute;
    background: radial-gradient(ellipse at center, rgba(63,160,30,.9), rgba(110,200,60,.5) 45%, rgba(255,255,255,0) 72%);
  }
  .foliage-left { left: -40px; top: 30px; width: 110px; height: 170px; }
  .foliage-right { right: -40px; top: -50px; width: 200px; height: 110px; }
  .appointment-title {
    position: absolute; left: 0; right: 0; top: 30px; text-align: center;
    font-size: 17px; font-weight: 700; color: var(--leaf-green);
  }
  .title-rule {
    position: absolute; left: 150px; right: 70px; top: 62px;
    border-bottom: 2px dotted var(--ink);
  }
  .form-row {
    position: absolute; left: 70px; right: 40px; display: flex; align-items: flex-end;
    font-size: 13px; font-weight: 700; color: var(--ink); white-space: nowrap;
  }
  .fill-line { flex: 1; border-bottom: 2px dotted var(--ink); margin: 0 10px 3px 4px; }
  .fill-line.short { flex: 0 0 120px; }
  .row-name { top: 90px; }
  .row-date { top: 130px; }
  .period { font-weight: 400; }
  .weekdays {
    position: absolute; left: 70px; top: 178px; display: flex; gap: 12px; list-style: none;
  }
  .weekdays li { display: flex; align-items: center; gap: 5px; font-size: 12px; color: var(--leaf-green); }
  .tick-box { width: 17px; height: 17px; border: 1.5px solid var(--box-line); background: var(--card-white); }
  .notice {
    position: absolute; left: 0; right: 0; top: 232px; text-align: center;
    font-size: 13px; font-weight: 700; color: var(--leaf-green);
  }
</style>
</head>
<body>
<main class="sheet">
  <section class="card card-front">
    <div class="front-artwork" role="img" aria-label="Soft-focus photograph of fresh green leaves on a sprig"></div>
    <div class="front-details">
      <h1 class="holder-name">Tom Rudd</h1>
      <p class="holder-role">Naturopath</p>
      <p class="holder-credentials">BHSc (Naturopathy) Member WHPG</p>
      <ul class="contact-list">
        <li>0487 925 316
          <svg class="contact-icon" viewBox="0 0 24 24" aria-hidden="true"><path fill="var(--leaf-green)" d="M6.6 10.8a15.1 15.1 0 0 0 6.6 6.6l2.2-2.2c.3-.3.7-.4 1-.2 1.1.4 2.3.6 3.6.6.6 0 1 .4 1 1V20c0 .6-.4 1-1 1C10.6 21 3 13.4 3 4c0-.6.4-1 1-1h3.5c.6 0 1 .4 1 1 0 1.3.2 2.5.6 3.6.1.3 0 .7-.2 1z"/></svg>
        </li>
        <li>tom.rudd@mailexample.com
          <svg class="contact-icon" viewBox="0 0 24 24" aria-hidden="true"><rect x="2" y="5" width="20" height="14" fill="var(--leaf-green)"/><polyline points="2,5 12,13 22,5" fill="none" stroke="#fff" stroke-width="2"/></svg>
        </li>
      </ul>
    </div>
  </section>

  <section class="card card-back">
    <div class="foliage foliage-left" role="img" aria-label="Cluster of green leaves at the left edge"></div>
    <div class="foliage foliage-right" role="img" aria-label="Cluster of green leaves at the top right corner"></div>
    <h2 class="appointment-title">Your Next Appointment on</h2>
    <div class="title-rule"></div>
    <div class="form-row row-name">Name :<span class="fill-line"></span>Time :<span class="fill-line short"></span><span class="period">AM / PM</span></div>
    <div class="form-row row-date">Date :<span class="fill-line short"></span></div>
    <ul class="weekdays">
      <li><span class="tick-box"></span>MON</li>
      <li><span class="tick-box"></span>TUE</li>
      <li><span class="tick-box"></span>WED</li>
      <li><span class="tick-box"></span>THU</li>
      <li><span class="tick-box"></span>FRI</li>
      <li><span class="tick-box"></span>SAT</li>
    </ul>
    <p class="notice">If unable to keep appointment, kindly give 24hrs notice.</p>
  </section>
</main>
</body>
</html>
```